Upscale business cards needed for Board of Directors

We need professional business cards created for members of our family business Board of Directors. We would like these relatively simple and straightforward, but also with a unique element to set them apart. Probably stick with neutral and simple colors - white, grey etc. We need space for the traditional elements, including name, title, address, email/phone number. And we will be creating several from this template so it needs to be template that is easy to switch information in and out of.
Business
See description

```html
<!DOCTYPE html>
<html lang="en">
<head>
<meta charset="utf-8">
<title>Bramwell Holdings — Business Card</title>
<link rel="stylesheet" href="https://fonts.googleapis.com/css2?family=Lato:wght@400;700;900&display=swap">
<style>
  :root {
    --ink: #0b0b0b;
    --paper: #ffffff;
    --gold: #b9a57a;
    --stage: #3a3a3a;
    --card-w: 600px;
    --card-h: 343px;
  }
  * { margin: 0; padding: 0; box-sizing: border-box; }
  html, body {
    width: 1200px; height: 900px; overflow: hidden;
    background: var(--stage);
    font-family: "Lato", Arial, sans-serif;
  }
  .canvas { position: relative; width: 1200px; height: 900px; }

  .card {
    position: absolute;
    width: var(--card-w); height: var(--card-h);
    overflow: hidden;
    box-shadow: 0 14px 30px rgba(0,0,0,.45);
  }

  /* Back side */
  .card--back { left: 520px; top: 70px; background: var(--ink); color: var(--paper); }
  .card--back .wordmark { position: absolute; left: 0; right: 0; top: 92px; text-align: center; }
  .card--back .site {
    position: absolute; left: 0; right: 0; top: 262px;
    text-align: center; font-size: 15px; letter-spacing: 2px; color: var(--paper);
  }

  .wordmark { font-weight: 900; text-transform: uppercase; line-height: 1; }
  .wordmark__main { display: block; font-size: 58px; letter-spacing: 1px; }
  .wordmark__sub { display: block; font-size: 24px; letter-spacing: 16px; margin-top: 8px; }

  /* Front side */
  .card--front { left: 80px; top: 470px; background: var(--paper); }
  .card--front .shape { position: absolute; inset: 0; }
  .card--front .wordmark { position: absolute; left: 40px; top: 44px; color: var(--ink); }
  .card--front .wordmark__main { font-size: 52px; }
  .card--front .wordmark__sub { font-size: 22px; letter-spacing: 14px; padding-left: 4px; }

  .address {
    position: absolute; left: 30px; top: 210px;
    color: var(--paper); font-size: 15px; line-height: 1.35;
  }
  .person { position: absolute; right: 30px; top: 192px; text-align: right; }
  .person__name { color: var(--paper); font-size: 24px; font-weight: 400; }
  .person__title { color: var(--gold); font-size: 15px; margin-top: 2px; }

  .contacts { position: absolute; right: 30px; top: 254px; list-style: none; }
  .contacts li {
    display: flex; justify-content: flex-end; align-items: center; gap: 10px;
    color: var(--paper); font-size: 14px; line-height: 19px;
  }
  .contacts svg { width: 13px; height: 13px; fill: var(--gold); flex: none; }
</style>
</head>
<body>
<main class="canvas">

  <section class="card card--back" aria-label="Card back">
    <div class="wordmark">
      <span class="wordmark__main">Bramwell</span>
      <span class="wordmark__sub">Holdings</span>
    </div>
    <p class="site">www.bramwellgroup.com</p>
  </section>

  <section class="card card--front" aria-label="Card front">
    <svg class="shape" viewBox="0 0 600 343" preserveAspectRatio="none" aria-hidden="true">
      <path d="M0,160 C150,235 390,262 600,112 L600,343 L0,343 Z" fill="#0b0b0b"/>
      <path d="M300,244 C440,244 545,190 600,108 L600,120 C548,205 440,256 300,244 Z" fill="#b9a57a"/>
    </svg>

    <div class="wordmark">
      <span class="wordmark__main">Bramwell</span>
      <span class="wordmark__sub">Holdings</span>
    </div>

    <address class="address" style="font-style:normal">
      1450 Cedar Lane<br>Marlow TX 78010
    </address>

    <div class="person">
      <p class="person__name">Daniel Whitford</p>
      <p class="person__title">Director</p>
    </div>

    <ul class="contacts">
      <li>512 555 0140
        <svg viewBox="0 0 24 24" aria-label="Phone"><path d="M6.6 10.8a15 15 0 0 0 6.6 6.6l2.2-2.2a1 1 0 0 1 1-.25 11.4 11.4 0 0 0 3.6.57 1 1 0 0 1 1 1V20a1 1 0 0 1-1 1A17 17 0 0 1 3 4a1 1 0 0 1 1-1h3.5a1 1 0 0 1 1 1c0 1.25.2 2.45.57 3.57a1 1 0 0 1-.25 1z"/></svg>
      </li>
      <li>512 555 0141
        <svg viewBox="0 0 24 24" aria-label="Fax"><path d="M6 2h12v5H6z M4 8h16a2 2 0 0 1 2 2v7h-4v5H6v-5H2v-7a2 2 0 0 1 2-2z M8 15v5h8v-5z"/></svg>
      </li>
      <li>info@bramwellgroup.com
        <svg viewBox="0 0 24 24" aria-label="Email"><path d="M2 5h20v14H2z M3.5 6.5 12 13l8.5-6.5" stroke="#0b0b0b" stroke-width="1.5"/></svg>
      </li>
      <li>www.bramwellgroup.com
        <svg viewBox="0 0 24 24" aria-label="Website"><circle cx="12" cy="12" r="10"/><path d="M2 12h20M12 2c3 3 3 17 0 20M12 2c-3 3-3 17 0 20M4 7h16M4 17h16" stroke="#0b0b0b" stroke-width="1.2" fill="none"/></svg>
      </li>
    </ul>
  </section>

</main>
</body>
</html>
```